Goodlooking website for a company who is working in the IT consultancy

We want a new website designed in WordPress. You can take www.vantoro.nl as an example. It should be a website with some short blocks of information about the company, nice pictures of our partners and our employees. A job page with a clear filter.

Target Market(s)

B2B

Industry/Entity Type

It Company

Coding

Coded - Design and coding required

Number of Pages Required

5+ page

Font styles to use
Sans Serif

Colors
0455a3
34a7d8

Requirements
Must have
• Check briefing

```html
<!DOCTYPE html>
<html lang="en">
<head>
<meta charset="utf-8">
<title>Nexora – Critical IT Systems</title>
<link rel="stylesheet" href="https://fonts.googleapis.com/css2?family=Lato:wght@400;700&family=Cinzel:wght@700&family=Orbitron:wght@700&display=swap">
<style>
:root{
  --green:#1a9a7e;
  --blue:#1e9bc9;
  --blue-deep:#0455a3;
  --ink:#2b2b2b;
  --muted:#8a8a8a;
  --line:#dcdcdc;
  --band:#e9ebec;
  --reply:#e3f4f9;
  --dark:#1d3b3a;
  --white:#fff;
}
*{margin:0;padding:0;box-sizing:border-box}
html,body{width:1200px;height:2980px;overflow:hidden;background:var(--white)}
body{position:relative;font-family:"Lato",sans-serif;color:var(--ink)}
.abs{position:absolute}
/* header */
.site-header{position:absolute;left:0;top:0;width:1200px;height:100px;background:var(--white)}
.brand{position:absolute;left:100px;top:22px;display:flex;align-items:center;gap:14px}
.brand-dot{width:56px;height:56px;border-radius:50%;background:var(--green)}
.brand-name{font-family:"Lato",sans-serif;font-weight:700;font-size:34px;letter-spacing:3px;color:var(--ink)}
.main-nav{position:absolute;left:406px;top:38px;display:flex;gap:50px;font-size:16px}
.main-nav a{color:var(--ink);text-decoration:none}
.search-icon{position:absolute;left:952px;top:40px}
.sign-in{position:absolute;left:1000px;top:32px;width:102px;height:38px;background:var(--blue);color:#fff;font-size:15px;font-weight:700;display:flex;align-items:center;justify-content:center;gap:6px;border-radius:2px}
/* hero */
.hero{position:absolute;left:0;top:100px;width:1200px;height:620px}
.hero-title{position:absolute;left:0;top:200px;width:1200px;text-align:center;font-family:"Orbitron",sans-serif;font-size:58px;color:#fff}
.hero-sub{position:absolute;left:0;top:284px;width:1200px;text-align:center;font-size:20px;font-weight:700;color:#fff}
.btn{display:inline-flex;align-items:center;gap:8px;color:#fff;font-weight:700;text-transform:uppercase;border-radius:2px}
.btn-green{background:var(--green)}
.btn-blue{background:var(--blue)}
.hero .btn{position:absolute;left:512px;top:338px;height:44px;padding:0 16px;font-size:15px}
/* section titles */
.section-title{font-family:"Cinzel",serif;font-size:36px;color:var(--ink);letter-spacing:1px}
/* about */
.about-text{position:absolute;left:100px;top:850px;width:490px;font-size:12.5px;line-height:30px;color:var(--muted)}
.about-text p+p{margin-top:2px}
.about-media{position:absolute;left:628px;top:794px;width:470px;height:334px;border:4px solid #fff;box-shadow:0 0 6px rgba(0,0,0,.18);background:radial-gradient(circle at 50% 55%,#0e5a6a,#0a2638 70%)}
/* what we do */
.what-band{position:absolute;left:0;top:1220px;width:1200px;height:520px;background:var(--band)}
.service{position:absolute;width:330px}
.service h3{font-size:20px;font-weight:700;color:var(--ink)}
.service p{font-size:12.5px;line-height:28px;color:var(--muted);margin-top:6px}
.service .more{font-size:13px;color:var(--blue);margin-top:2px}
.service.left{text-align:right}
.icon-circle{position:absolute;width:102px;height:102px;border-radius:50%;display:flex;align-items:center;justify-content:center}
/* jobs */
.job-tab{position:absolute;left:100px;width:298px;height:48px;display:flex;align-items:center;justify-content:space-between;padding:0 20px;font-size:16px;text-transform:uppercase}
.job-tab.open{background:var(--green);color:#fff}
.job-tab.closed{border:1px solid var(--green);color:var(--green)}
.job-detail{position:absolute;left:434px;top:1908px;width:360px}
.job-detail h4{font-size:18px;font-weight:400;color:var(--ink)}
.job-detail p{font-size:12.5px;line-height:31px;color:var(--muted);margin-top:8px}
.job-links{margin-top:10px}
.job-links a{display:block;font-size:17px;color:var(--ink);text-decoration:underline;line-height:32px}
.job-detail .btn{margin-top:24px;height:40px;padding:0 20px;font-size:14px}
.reply{position:absolute;left:818px;top:1910px;width:286px;height:380px;background:var(--reply);padding:28px 26px}
.reply h5{font-size:21px;font-weight:400;color:var(--ink)}
.field{height:38px;background:#fff;border:1px solid #e2e2e2;margin-top:8px;font-size:12px;color:var(--muted);display:flex;align-items:center;padding-left:20px}
.reply h5+.field{margin-top:14px}
.upload{display:flex;align-items:center;margin-top:10px;font-size:12px;color:var(--muted)}
.upload span{width:80px}
.upload .select{width:152px;height:38px;background:var(--blue);color:#fff;display:flex;align-items:center;justify-content:center;font-size:13px}
.progress{height:8px;background:var(--green);margin-top:12px;border-radius:4px}
.no-file{font-size:12px;color:var(--green);text-align:center;margin-top:12px}
.send{height:38px;background:var(--blue);color:#fff;font-weight:700;display:flex;align-items:center;justify-content:center;margin-top:8px;font-size:14px}
.divider{position:absolute;left:100px;top:2354px;width:1000px;height:1px;background:var(--line)}
.partner{position:absolute;top:2424px;width:204px;height:86px;border:1px solid var(--line);display:flex;align-items:center;justify-content:center}
.partner i{display:block;width:120px;height:46px;background:#c9d1d6}
/* footer */
.site-footer{position:absolute;left:0;top:2590px;width:1200px;height:390px}
.foot-brand{position:absolute;left:160px;top:2752px;display:flex;align-items:center;gap:14px;color:#fff}
.foot-brand .brand-dot{background:#fff;width:58px;height:58px}
.foot-brand .brand-name{color:#fff;font-size:32px}
.foot-col{position:absolute;top:2732px;color:#fff}
.foot-col h6{font-size:20px;font-weight:400;text-decoration:underline;margin-bottom:12px}
.foot-col p{font-size:13px;line-height:23px}
.contact-row{display:flex;align-items:center;gap:14px;margin-bottom:12px;font-size:13px;line-height:21px}
.contact-row .ci{width:38px;height:38px;border:1px solid #fff;border-radius:50%;display:flex;align-items:center;justify-content:center;flex:none}
.follow{position:absolute;left:158px;top:2844px;color:#fff;font-size:20px;text-decoration:underline}
.social{position:absolute;top:2888px;width:38px;height:38px;border:1px solid #fff;border-radius:50%}
.copyright{position:absolute;left:428px;top:2894px;color:#fff;font-size:12px}
</style>
</head>
<body>

<header class="site-header">
  <div class="brand"><span class="brand-dot"></span><span class="brand-name">NEXORA</span></div>
  <nav class="main-nav"><a>Home</a><a>Our solutions</a><a>Our team</a><a>Jobs</a><a>Contact</a></nav>
  <svg class="search-icon" width="18" height="18" viewBox="0 0 18 18"><circle cx="7.5" cy="7.5" r="5.5" fill="none" stroke="#1e9bc9" stroke-width="2.2"/><line x1="11.5" y1="11.5" x2="16" y2="16" stroke="#1e9bc9" stroke-width="2.4"/></svg>
  <div class="sign-in"><svg width="12" height="13" viewBox="0 0 12 13"><circle cx="6" cy="3.5" r="3" fill="#fff"/><path d="M0 13Q0 7 6 7Q12 7 12 13Z" fill="#fff"/></svg>SIGN IN</div>
</header>

<section class="hero">
  <svg class="abs" style="left:0;top:0" width="1200" height="620" viewBox="0 0 1200 620">
    <defs>
      <linearGradient id="heroShade" x1="0" y1="0" x2="1" y2="1">
        <stop offset="0" stop-color="#5c6a70"/><stop offset=".5" stop-color="#3c464b"/><stop offset="1" stop-color="#252c30"/>
      </linearGradient>
    </defs>
    <path d="M0 0H1200V460Q600 720 0 460Z" fill="url(#heroShade)" role="img" aria-label="Photo of hands joining puzzle pieces over a network of people icons"/>
    <path d="M210 530Q600 720 990 530Q600 680 210 530Z" fill="#1e9bc9"/>
    <g fill="#fff" stroke="#fff" stroke-width="1.5">
      <circle cx="562" cy="515" r="5"/><circle cx="582" cy="515" r="5" fill="none"/><circle cx="602" cy="515" r="5" fill="none"/><circle cx="622" cy="515" r="5" fill="none"/><circle cx="642" cy="515" r="5" fill="none"/>
    </g>
  </svg>
  <h1 class="hero-title">Welcome to Nexora</h1>
  <p class="hero-sub">We build mission critical environments</p>
  <a class="btn btn-green">Quick contact <svg width="14" height="14" viewBox="0 0 14 14"><circle cx="7" cy="7" r="7" fill="#fff"/><path d="M5.5 4L8.5 7L5.5 10" stroke="#1a9a7e" stroke-width="2" fill="none"/></svg></a>
</section>

<section class="about">
  <h2 class="section-title abs" style="left:100px;top:796px">ABOUT US</h2>
  <div class="about-text">
    <p>Nexora provides services that ensure that your "automation" is automated. Within IT environments repetitive tasks often take place that take unnecessarily long periods of time and are also prone to error. A comma forgotten or not executing a command can have major consequences for the service.</p>
    <p>Automating these tasks ensures that you always play a reliable process with known outcomes. It also gives the internal team more time to focus on innovations, new techniques or improvements within your own services.</p>
  </div>
  <a class="btn btn-green abs" style="left:100px;top:1080px;height:38px;padding:0 14px;font-size:14px;text-transform:none">Read more <svg width="13" height="13" viewBox="0 0 14 14"><circle cx="7" cy="7" r="7" fill="#fff"/><path d="M5.5 4L8.5 7L5.5 10" stroke="#1a9a7e" stroke-width="2" fill="none"/></svg></a>
  <div class="about-media" role="img" aria-label="Illustration of an infinity loop with the stages plan, code, build, test, release, deploy, operate, monitor"></div>
</section>

<section class="what-band">
  <h2 class="section-title abs" style="left:0;top:82px;width:1200px;text-align:center">WHAT WE DO</h2>
</section>
<div class="service left" style="left:138px;top:1386px"><h3>Automation &amp; Deployment</h3><p>Nexora provides services that ensure that your "automation" is automated. Within IT environments</p><div class="more">Read More »</div></div>
<div class="service left" style="left:138px;top:1534px"><h3>Cloud Consultancy</h3><p>Cloud services are nowadays an indispensable part of the IT landscape. Where previously an application</p><div class="more">Read More »</div></div>
<div class="service" style="left:732px;top:1386px"><h3>Mission Critical Solutions</h3><p>Nexora is the specialist in the construction and management of Mission Critical Systems.</p><div class="more">Read More »</div></div>
<div class="service" style="left:732px;top:1534px"><h3>Hyperconverged Infrastructures</h3><p>Among other things, Nexora supplies Stratanode products in which computing power, storage and networks</p><div class="more">Read More »</div></div>

<div class="icon-circle" style="left:484px;top:1392px;background:var(--green)"><svg width="46" height="40" viewBox="0 0 46 40" fill="none" stroke="#fff" stroke-width="2.5"><rect x="3" y="3" width="40" height="26" rx="2"/><path d="M16 37H30M23 29V37"/></svg></div>
<div class="icon-circle" style="left:616px;top:1392px;background:#263238"><svg width="40" height="40" viewBox="0 0 40 40" fill="none" stroke="#fff" stroke-width="2.5"><path d="M8 32L14 26M24 6C32 4 36 8 34 16L20 30L10 20Z"/><circle cx="25" cy="15" r="3"/></svg></div>
<div class="icon-circle" style="left:484px;top:1542px;background:#263238"><svg width="46" height="32" viewBox="0 0 46 32" fill="none" stroke="#fff" stroke-width="2.5"><path d="M12 28H36A8 8 0 0 0 35 12A11 11 0 0 0 14 10A9 9 0 0 0 12 28Z"/></svg></div>
<div class="icon-circle" style="left:616px;top:1542px;background:var(--blue)"><svg width="44" height="36" viewBox="0 0 44 36" fill="none" stroke="#fff" stroke-width="2.5"><rect x="3" y="3" width="11" height="11" rx="2"/><rect x="17" y="3" width="11" height="11" rx="2"/><rect x="31" y="3" width="10" height="11" rx="2"/><rect x="3" y="21" width="11" height="11" rx="2"/><rect x="17" y="21" width="11" height="11" rx="2"/><rect x="31" y="21" width="10" height="11" rx="2"/></svg></div>

<section class="jobs">
  <h2 class="section-title abs" style="left:0;top:1822px;width:1200px;text-align:center">OUR JOBS</h2>
  <div class="job-tab open" style="top:1912px">Kernix Engineer <svg width="16" height="16" viewBox="0 0 16 16"><circle cx="8" cy="8" r="8" fill="#fff"/><path d="M4.5 8H11.5" stroke="#1a9a7e" stroke-width="2"/></svg></div>
  <div class="job-tab closed" style="top:1968px">Meridian Engineer <svg width="16" height="16" viewBox="0 0 16 16"><circle cx="8" cy="8" r="8" fill="#1a9a7e"/><path d="M4.5 8H11.5M8 4.5V11.5" stroke="#fff" stroke-width="2"/></svg></div>
  <div class="job-detail">
    <h4>Organization / Department</h4>
    <p>You will work in a team with Kernix engineers from Nexora BV. This team is used by our large customers. You will have an independent position with nice clients. You do not have to worry about the facilities and reward, which is excellent. But what we find more important is that you bring knowledge to our relationships.</p>
    <div class="job-links"><a>Function information</a><a>Job requirements</a><a>offer</a></div>
    <a class="btn btn-blue">Upload CV <svg width="13" height="13" viewBox="0 0 14 14"><circle cx="7" cy="7" r="7" fill="#fff"/><path d="M5.5 4L8.5 7L5.5 10" stroke="#1e9bc9" stroke-width="2" fill="none"/></svg></a>
  </div>
  <form class="reply">
    <h5>Reply</h5>
    <div class="field">Name</div>
    <div class="field">Email</div>
    <div class="field">Phone</div>
    <div class="upload"><span>Upload CV</span><div class="select">Select file</div></div>
    <div class="progress"></div>
    <div class="no-file">No file selected</div>
    <div class="send">SEND</div>
  </form>
  <div class="divider"></div>
  <div class="partner" style="left:166px"><i></i></div>
  <div class="partner" style="left:388px"><i></i></div>
  <div class="partner" style="left:608px"><i></i></div>
  <div class="partner" style="left:830px"><i></i></div>
</section>

<footer class="site-footer">
  <svg class="abs" style="left:0;top:0" width="1200" height="390" viewBox="0 0 1200 390">
    <defs>
      <linearGradient id="footShade" x1="0" y1="0" x2="0" y2="1">
        <stop offset="0" stop-color="#2a4f4c"/><stop offset="1" stop-color="#16302f"/>
      </linearGradient>
    </defs>
    <path d="M220 80Q600 -40 980 80Q600 -15 220 80Z" fill="#1e9bc9"/>
    <path d="M0 140Q600 -40 1200 140V390H0Z" fill="url(#footShade)" role="img" aria-label="Photo of a city skyline at dusk"/>
  </svg>
</footer>
<div class="foot-brand"><span class="brand-dot"></span><span class="brand-name">NEXORA</span></div>
<div class="foot-col" style="left:424px"><h6>Vacancies</h6><p>Kernix Engineer<br>Meridian Engineer</p></div>
<div class="foot-col" style="left:596px"><h6>Latest news</h6><p>Website Nexora live!<br>Nexora visited Meridian Tech Event.<br>Nexora has become a Redwing partner.</p></div>
<div class="foot-col" style="left:874px"><h6>NEXORA</h6>
  <div class="contact-row"><span class="ci"><svg width="16" height="16" viewBox="0 0 16 16"><path d="M8 2L1 8H3V14H13V8H15Z" fill="#fff"/></svg></span><span>Harmonielaan 14,<br>3521 KB Veldhoven</span></div>
  <div class="contact-row"><span class="ci"><svg width="16" height="16" viewBox="0 0 16 16"><path d="M3 1L6 1L7 5L5 6.5Q6.5 9.5 9.5 11L11 9L15 10V13Q15 15 13 15Q1 14 1 3Q1 1 3 1Z" fill="#fff"/></svg></span><span>085-3127740</span></div>
  <div class="contact-row"><span class="ci"><svg width="16" height="12" viewBox="0 0 16 12"><rect x="0" y="0" width="16" height="12" fill="#fff"/><path d="M0 0L8 7L16 0" stroke="#1d3b3a" stroke-width="1.5" fill="none"/></svg></span><span>info@nexora.nl</span></div>
</div>
<div class="follow">Follow us</div>
<span class="social" style="left:158px"></span>
<span class="social" style="left:204px"></span>
<div class="copyright">© copyright 2018 Nexora .All Rights Reserved &nbsp;|&nbsp; Privacy policy</div>

</body>
</html>
```